Business Card and Letterhead for Pimlu - modern real estate business

I need a double sided business card design for Pimlu. Please see business card brief here https://files.trelvonadocs.com/sheet/r/7QzTmWbaXLJnoPEd-kRyUgFhHsstbvCe2qfoMxDa_pz/view?mode=shared

Please feel free to design the business cards however you feel best. I am happy to give some creative freedoms and then provide feedback from there.

Please then also create a letterhead to match the business card design

Colors

Designer to choose colors to be used in the design.

Requirements
Must have
• Must be a modern, elegant business card which looks very professional

```html
<!DOCTYPE html>
<html lang="en">
<head>
<meta charset="utf-8">
<title>Pimlu Letterhead</title>
<link href="https://fonts.googleapis.com/css2?family=Oswald:wght@600&family=Source+Sans+3:wght@400;700&display=swap" rel="stylesheet">
<style>
  :root {
    --backdrop: #222829;
    --paper: #f6f9fa;
    --brand-red: #f20500;
    --brand-black: #050708;
    --ink: #141414;
  }
  * { margin: 0; padding: 0; box-sizing: border-box; }
  html, body { width: 1119px; height: 1200px; overflow: hidden; background: var(--backdrop); }
  body { font-family: "Source Sans 3", "Myriad Pro", sans-serif; color: var(--ink); }

  .letterhead {
    position: absolute; left: 179px; top: 85px;
    width: 752px; height: 973px; background: var(--paper);
  }

  .band { position: absolute; }
  .band--black { background: var(--brand-black); }
  .band--red { background: var(--brand-red); }

  .header-block { position: absolute; top: 94px; height: 44px; }
  .header-block .band--black { top: 0; height: 22px; left: 0; right: 0; }
  .header-block .band--red { top: 22px; height: 22px; left: 0; right: 0; }
  .header-block--left { left: 0; width: 40px; }
  .header-block--tick { left: 493px; width: 11px; }
  .header-block--right { left: 620px; width: 132px; }

  .wordmark {
    position: absolute; left: 53px; top: 87px;
    font-family: "Source Sans 3", sans-serif; font-weight: 700;
    font-size: 58px; line-height: 58px; letter-spacing: 2px;
    color: var(--brand-red);
  }

  .contact-list { position: absolute; right: 147px; top: 94px; list-style: none; }
  .contact-list li {
    display: flex; align-items: center; justify-content: flex-end;
    font-size: 8px; height: 16px; gap: 7px; white-space: nowrap;
  }
  .contact-list li:nth-child(3) { margin-top: 2px; }
  .contact-list svg { width: 9px; height: 9px; fill: var(--brand-black); }

  .subject {
    position: absolute; left: 0; right: 0; top: 247px; text-align: center;
    font-family: "Oswald", "Futura", sans-serif; font-weight: 600;
    font-size: 22px; line-height: 32px; letter-spacing: -0.2px; color: var(--ink);
  }

  .body-copy { position: absolute; left: 131px; top: 322px; width: 492px; font-size: 14.2px; line-height: 17.7px; }
  .body-copy p { margin-bottom: 17.7px; }
  .body-copy .ln { display: block; white-space: nowrap; }
  .body-copy .ln.j { text-align: justify; text-align-last: justify; white-space: normal; }

  .about { position: absolute; left: 0; right: 0; top: 820px; text-align: center; }
  .about__title { font-size: 15px; line-height: 18px; font-weight: 400; }
  .about__rule {
    width: 90px; height: 1px; margin: 2px auto 3px;
    background: linear-gradient(90deg, transparent, var(--brand-red), transparent);
  }
  .about__text { font-size: 12.2px; line-height: 14.8px; white-space: nowrap; }
  .about__rule--wide { width: 130px; margin: 5px auto 2px; }
  .about__licence { font-size: 14.8px; line-height: 17px; }

  .footer-bands { position: absolute; left: 0; right: 0; bottom: 0; height: 45px; }
  .footer-bands .band--black { top: 0; height: 23px; left: 0; right: 0; }
  .footer-bands .band--red { top: 23px; height: 22px; left: 0; right: 0; }
</style>
</head>
<body>
  <div class="letterhead">
    <div class="header-block header-block--left"><div class="band band--black"></div><div class="band band--red"></div></div>
    <div class="wordmark">PIMLU</div>
    <div class="header-block header-block--tick"><div class="band band--black"></div><div class="band band--red"></div></div>

    <ul class="contact-list">
      <li>info@pimlu.com
        <svg viewBox="0 0 10 10" aria-hidden="true"><path d="M0 2h10v6H0z M0 2l5 3.5L10 2" fill="var(--brand-black)" stroke="var(--paper)" stroke-width="0.8"/></svg>
      </li>
      <li>02 5189 3407
        <svg viewBox="0 0 10 10" aria-hidden="true"><path d="M2 0.5l2 2-1 1.3c.6 1.4 1.6 2.4 3 3l1.3-1 2 2-1.3 1.7C4.5 9.3.7 5.5.3 1.8z"/></svg>
      </li>
      <li>Harlow Vale NSW 2790
        <svg viewBox="0 0 10 10" aria-hidden="true"><path d="M5 0C3 0 1.6 1.5 1.6 3.4 1.6 6 5 10 5 10s3.4-4 3.4-6.6C8.4 1.5 7 0 5 0zm0 4.8a1.4 1.4 0 110-2.8 1.4 1.4 0 010 2.8z"/></svg>
      </li>
    </ul>
    <div class="header-block header-block--right"><div class="band band--black"></div><div class="band band--red"></div></div>

    <h1 class="subject">SUBJECT HEADLEINE HERE &amp; USED FUTURA BOLD FONT</h1>

    <div class="body-copy">
      <p>
        <span class="ln j">Lorem ipsum dolor sit amet, consectetuer adipiscing elit, sed diam nonummy</span>
        <span class="ln j">nibh euismod tincidunt ut laoreet dolore magna aliquam erat volutpat. Ut wisi</span>
        <span class="ln j">enim ad minim veniam, quis nostrud exerci tation ullamcorper suscipit lobortis</span>
        <span class="ln j">nisl ut aliquip ex ea commodo consequat. Duis autem vel eum iriure dolor in hen-</span>
        <span class="ln j">drerit in vulputate velit esse molestie consequat, vel illum dolore eu feugiat nulla</span>
        <span class="ln j">facilisis at vero eros et accumsan et iusto odio dignissim qui blandit praesent</span>
        <span class="ln j">luptatum zzril delenit augue duis dolore te feugait nulla facilisi.</span>
        <span class="ln">Lorem ipsum dolor sit amet, cons ectetuer adipiscing elit, sed diam nonummy</span>
        <span class="ln">nibh euismod tincidunt ut laoreet dolore magna aliquam erat volutpat. Ut wisi</span>
        <span class="ln">enim ad minim veniam, quis nostrud exerci tation ullamcorper suscipit lobortis</span>
        <span class="ln">nisl ut aliquip ex ea commodo consequat.</span>
      </p>
      <p>
        <span class="ln j">Lorem ipsum dolor sit amet, consectetuer adipiscing elit, sed diam nonummy</span>
        <span class="ln j">nibh euismod tincidunt ut laoreet dolore magna aliquam erat volutpat. Ut wisi</span>
        <span class="ln j">enim ad minim veniam, quis nostrud exerci tation ullamcorper suscipit lobortis</span>
        <span class="ln j">nisl ut aliquip ex ea commodo consequat. Duis autem vel eum iriure dolor in hen-</span>
        <span class="ln j">drerit in vulputate velit esse molestie consequat, vel illum dolore eu feugiat nulla</span>
        <span class="ln j">facilisis at vero eros et accumsan et iusto odio dignissim qui blandit praesent</span>
        <span class="ln">luptatum zzril delenit augue duis dolore te feugait nulla facilisi.</span>
      </p>
      <p>
        <span class="ln j">Lorem ipsum dolor sit amet, cons ectetuer adipiscing elit, sed diam nonummy</span>
        <span class="ln j">nibh euismod tincidunt ut laoreet dolore magna aliquam erat volutpat. Ut wisi</span>
        <span class="ln j">enim ad minim veniam, quis nostrud exerci tation ullamcorper suscipit lobortis</span>
        <span class="ln">&nbsp;nisl ut aliquip ex ea commodo consequat.</span>
      </p>
    </div>

    <section class="about">
      <h2 class="about__title">ABOUT PIMLU</h2>
      <div class="about__rule"></div>
      <p class="about__text">At vero eos et accusamus et iusto odio dignis simos ducimus qui blanditiis praesentium voluptatum deleniti atque<br>corrupti quos dolores et quas mol estias excepturi sint occaecati cupiditate non pro vident, similique sunt in culpa<br>qui officia deserunt mollitia animi, id est laborum et dolorum fuga.</p>
      <div class="about__rule about__rule--wide"></div>
      <p class="about__licence">Lic No. 40817266</p>
    </section>

    <div class="footer-bands"><div class="band band--black"></div><div class="band band--red"></div></div>
  </div>
</body>
</html>
```